Business Card Design

I need a business card for a new company based in Australia called "MedLinkora".

Its a cloud program for GPs that allows them to search for the specialist they require using a simple user friendly tool.

I would like the colours to match those in the program (the colours in the logo attached).

The final design should reflect the programs clarity, ease of use and professionalism.

Target Market(s)

GPs and other Health Professionals

Industry/Entity Type

Business

Contact Information for Business Card

MedLinkora; The Whole Consultant Index; Marla Voss CEO; 0438215967; marla@medlinkora.example; www.medlinkora.example

Requirements
Must have
• Must have the logo attached; the web address and my name and phone number
Nice to have
• the slogan "The Whole Consultant Index"

```html
<!DOCTYPE html>
<html lang="en">
<head>
<meta charset="utf-8">
<title>MedLinkora Business Card</title>
<link rel="stylesheet" href="https://fonts.googleapis.com/css2?family=Open+Sans:wght@400;600;700&display=swap">
<style>
  :root {
    --brand-blue: #16b2e6;
    --band-grey: #8c8e91;
    --curl-grey: #c9cbcd;
    --ink: #3a3a3c;
    --tagline-grey: #8a8a8a;
    --paper: #ffffff;
    --backdrop: #eceae6;
  }
  * { margin: 0; padding: 0; box-sizing: border-box; }
  html, body {
    width: 1200px; height: 829px; overflow: hidden;
    background: var(--backdrop);
    font-family: "Open Sans", Arial, sans-serif;
  }
  .sheet {
    position: relative; width: 1200px; height: 829px;
    display: flex; align-items: center; justify-content: center; gap: 60px;
  }
  .card {
    position: relative; width: 520px; height: 318px; overflow: hidden;
    box-shadow: 0 6px 18px rgba(0,0,0,0.18);
  }
  .card-front { background: var(--paper); }
  .card-back { background: var(--brand-blue); color: var(--paper); }

  .front-shapes { position: absolute; inset: 0; width: 100%; height: 100%; }
  .holder {
    position: absolute; top: 10px; right: 26px; text-align: right; color: var(--paper);
  }
  .holder-name { font-weight: 700; font-size: 15px; line-height: 1.2; }
  .holder-title { font-size: 10px; line-height: 1.3; }

  .wordmark {
    font-weight: 400; letter-spacing: -1px; line-height: 1;
  }
  .card-front .wordmark {
    position: absolute; left: 34px; top: 116px; font-size: 50px; color: var(--brand-blue);
  }
  .card-front .tagline {
    position: absolute; left: 38px; top: 170px; font-size: 14px; color: var(--tagline-grey);
  }
  .contacts {
    position: absolute; left: 38px; bottom: 28px; list-style: none;
    font-size: 15px; color: var(--ink); line-height: 1.55;
  }
  .contacts li { display: flex; align-items: center; gap: 10px; }
  .contacts svg { width: 15px; height: 15px; flex: none; }

  .back-lockup {
    position: absolute; left: 64px; top: 92px;
  }
  .card-back .wordmark { font-size: 66px; color: var(--paper); }
  .card-back .tagline { font-size: 18px; margin-top: 6px; margin-left: 4px; }
  .card-back .website {
    position: absolute; left: 120px; top: 220px; font-size: 17px; letter-spacing: 2px;
  }
</style>
</head>
<body>
<main class="sheet">
  <section class="card card-front" aria-label="Business card front">
    <svg class="front-shapes" viewBox="0 0 520 318" preserveAspectRatio="none" aria-hidden="true">
      <polygon points="120,82 165,54 420,54 430,82" fill="var(--band-grey)"/>
      <path d="M420,54 L520,54 L520,80 C470,80 440,86 430,82 Z" fill="var(--curl-grey)"/>
      <polygon points="165,54 230,0 520,0 520,54" fill="var(--brand-blue)"/>
    </svg>
    <div class="holder">
      <p class="holder-name">Marla Voss</p>
      <p class="holder-title">CEO</p>
    </div>
    <p class="wordmark">MedLinkora</p>
    <p class="tagline">The Whole Consultant Index</p>
    <ul class="contacts">
      <li>
        <svg viewBox="0 0 16 16" aria-hidden="true"><circle cx="8" cy="8" r="8" fill="var(--brand-blue)"/><path d="M5.5 4.5l1.5 0 .8 2-1 .8a5 5 0 0 0 2 2l.8-1 2 .8v1.5c0 .5-.5 1-1 1A7 7 0 0 1 4.5 5.5c0-.5.5-1 1-1z" fill="#fff"/></svg>
        0438215967
      </li>
      <li>
        <svg viewBox="0 0 16 16" aria-hidden="true"><circle cx="8" cy="8" r="8" fill="var(--brand-blue)"/><rect x="4" y="5" width="8" height="6" rx="1" fill="#fff"/><path d="M4 5.5l4 3 4-3" stroke="var(--brand-blue)" fill="none" stroke-width="1"/></svg>
        marla@medlinkora.example
      </li>
      <li>
        <svg viewBox="0 0 16 16" aria-hidden="true"><circle cx="8" cy="8" r="8" fill="var(--brand-blue)"/><circle cx="8" cy="8" r="4.5" fill="none" stroke="#fff" stroke-width="1"/><path d="M3.5 8h9M8 3.5c-2 2.5-2 6.5 0 9M8 3.5c2 2.5 2 6.5 0 9" fill="none" stroke="#fff" stroke-width="0.8"/></svg>
        www.medlinkora.example
      </li>
    </ul>
  </section>

  <section class="card card-back" aria-label="Business card back">
    <div class="back-lockup">
      <p class="wordmark">MedLinkora</p>
      <p class="tagline">The Whole Consultant Index</p>
    </div>
    <p class="website">www.medlinkora.example</p>
  </section>
</main>
</body>
</html>
```